Business Card Design Project

Basic business card with minimal details. I just need company name, email & web address, telephone and my name.
I would like the back of the card to be grey with my logo & company name centred.

Target Market(s)

Architects
Builders
Property Developers

Industry/Entity Type

Business

Font styles to use
Sans Serif

Colors

Designer to choose colors to be used in the design.

Requirements
Must have
• Tallow Crest
Rupert Hazelby - Director
M: 0427 915203
E: rupert@tallowcrest.com.au
W: www.tallowcrest.com.au
Should not have
• No other images or pictures

```html
<!DOCTYPE html>
<html lang="en">
<head>
<meta charset="utf-8">
<title>Tallow Crest – Business Card</title>
<link rel="stylesheet" href="https://fonts.googleapis.com/css2?family=Lato:wght@400;700&display=swap">
<style>
  :root {
    --stage: #e6e7e9;
    --card: #ffffff;
    --card-back: #5d6268;
    --back-text: #ffffff;
    --brand-red: #a3192f;
    --brand-slate: #3f4b57;
    --ink: #1a1a1a;
    --band: #0c0c0c;
    --band-text: #ffffff;
  }
  * { box-sizing: border-box; margin: 0; padding: 0; }
  html, body {
    width: 1200px; height: 926px; overflow: hidden;
    background: var(--stage);
    font-family: "Lato", Arial, sans-serif;
  }
  .stage { position: relative; width: 1200px; height: 926px; }
  .card {
    position: absolute; left: 300px;
    width: 600px; height: 367px;
    background: var(--card);
    box-shadow: 0 4px 14px rgba(0,0,0,.12);
    overflow: hidden;
  }
  .card--back { top: 60px; background: var(--card-back); }
  .card--front { top: 499px; }

  .brand {
    display: flex; align-items: center; justify-content: center; gap: 14px;
  }
  .brand__mark { width: 22px; height: 22px; background: var(--brand-red); }
  .brand__name {
    font-weight: 700; color: var(--brand-slate);
    letter-spacing: 4px; text-transform: uppercase;
  }
  .card--back .brand { height: 100%; }
  .card--back .brand__name { font-size: 36px; color: var(--back-text); }
  .card--back .brand__mark { width: 30px; height: 30px; }

  .card--front .brand { position: absolute; top: 48px; left: 0; right: 0; }
  .card--front .brand__name { font-size: 28px; }

  .holder {
    position: absolute; top: 118px; left: 0; right: 0;
    text-align: center; font-size: 32px; line-height: 40px;
    color: var(--brand-red); font-weight: 400;
  }
  .holder strong { font-weight: 700; }
  .holder-title {
    position: absolute; top: 160px; left: 0; right: 0;
    text-align: center; font-size: 13px; line-height: 18px;
    color: var(--brand-slate); letter-spacing: 3px; text-transform: uppercase;
  }

  .contact { position: absolute; font-size: 15px; line-height: 20px; color: var(--ink); letter-spacing: .4px; }
  .contact b { font-weight: 700; }
  .contact--mobile { top: 196px; left: 40px; }
  .contact--email { top: 222px; right: 40px; }

  .swoosh { position: absolute; left: 0; bottom: 0; width: 600px; height: 367px; }
  .website {
    position: absolute; left: 70px; top: 316px;
    font-size: 17px; line-height: 22px; font-weight: 700;
    color: var(--band-text); letter-spacing: 2.5px;
  }
</style>
</head>
<body>
<main class="stage">
  <section class="card card--back" aria-label="Card back">
    <div class="brand">
      <span class="brand__mark"></span>
      <span class="brand__name">Tallow Crest</span>
    </div>
  </section>

  <section class="card card--front" aria-label="Card front">
    <svg class="swoosh" viewBox="0 0 600 367" aria-hidden="true">
      <path d="M0 300 Q260 262 600 367 L0 367 Z" fill="var(--band)"/>
      <path d="M0 286 Q280 240 600 360 L600 367 Q280 252 0 294 Z" fill="var(--brand-red)"/>
      <path d="M0 294 Q280 252 600 367 L600 367 Q260 264 0 300 Z" fill="var(--card)"/>
    </svg>
    <div class="brand">
      <span class="brand__mark"></span>
      <span class="brand__name">Tallow Crest</span>
    </div>
    <h1 class="holder">Rupert <strong>Hazelby</strong></h1>
    <p class="holder-title">Director</p>
    <p class="contact contact--mobile"><b>mobile</b>: 0427 915203</p>
    <p class="contact contact--email"><b>email</b>: rupert@tallowcrest.com.au</p>
    <p class="website">www.tallowcrest.com.au</p>
  </section>
</main>
</body>
</html>
```